Business Cards for new orthopaedic surgery practice

My husband and I are starting our own orthopaedic surgery practice. We are looking for a business card that is uniform, but one will have my name/title and the other will have his. You can just create one design with my name on it for now. But when I choose your design as the winning design I will ask that you add another copy with his name/title.

We are looking for classy, simple, elite all in one. We like dark blues/a little gold/yellow. Something that goes with our logo. We want our logo incorporated. Here is all the info you need:
Business name: RV Bone & Vitality Center
Location: 38517 North Willowmere Ave
Brightwater Cove, FL 33490
Phone: 954-218-4063
Fax: 954-582-7341
Email: info@myrvbonecare.example

Names: Lydia Vance, M.D.
Board Certified Hand and Upper Extremity Surgeon

Ebo Dansu, M.D.
Board Certified Hip & Knee Replacement/General Orthopaedic Surgeon

Can decide what you want to put on the back. Maybe a slogan:
Grounded in Care. Centered on You

I am just going to upload our logo. The only thing is if we select you as the winning design, the location, and phone numbers may change. We will need your help to update that once fully solidified.

Industry/Entity Type

Medical

Contact Information for Business Card

Colors
0054AA
0677BA
7BADD7
CADEEF
E8F1F8
0094D4
00A9DD
6FCCEA
C7EBF8
E9F6FB

Requirements
Must have
• class, appeal,
Should not have
• We want to air on the side of masculine if we are looking at masculine vs. feminine feel. But we still want it classy, sophisticated, and something we will love

```html
<!DOCTYPE html>
<html lang="en">
<head>
<meta charset="utf-8">
<title>RV Bone &amp; Vitality Center — Business Card</title>
<link rel="stylesheet" href="https://fonts.googleapis.com/css2?family=Libre+Caslon+Text:wght@700&family=Mulish:wght@400;500&display=swap">
<style>
  :root {
    --stage: #1b1c1f;
    --navy: #1b2a52;
    --navy-soft: #2b3d6e;
    --gold: #c59a52;
    --paper: #f3f3f2;
    --ink-light: #eef1f7;
  }
  * { margin: 0; padding: 0; box-sizing: border-box; }
  html, body { width: 1200px; height: 1059px; overflow: hidden; background: var(--stage); }
  .stage { position: relative; width: 1200px; height: 1059px; }

  .card {
    position: absolute;
    width: 690px;
    height: 392px;
    border-radius: 18px;
    overflow: hidden;
    background: var(--navy);
  }
  .card--front { left: 256px; top: 89px; }
  .card--back { left: 255px; top: 547px; }

  .front-panel { position: absolute; inset: 0; width: 100%; height: 100%; }

  .contact {
    position: absolute;
    left: 39px;
    top: 50px;
    color: var(--ink-light);
    font-family: "Mulish", sans-serif;
    font-weight: 400;
  }
  .contact__name {
    font-family: "Libre Caslon Text", serif;
    font-weight: 700;
    font-size: 24px;
    letter-spacing: 0.3px;
    color: var(--gold);
    line-height: 1;
    white-space: nowrap;
  }
  .contact__title {
    margin-top: 8px;
    font-size: 17px;
    line-height: 23px;
  }
  .contact__address {
    position: absolute;
    top: 146px;
    font-size: 17px;
    line-height: 25px;
    white-space: nowrap;
  }
  .contact__lines {
    position: absolute;
    top: 212px;
    list-style: none;
    font-size: 17px;
    white-space: nowrap;
  }
  .contact__lines li {
    display: flex;
    align-items: center;
    height: 29px;
  }
  .contact__lines svg { width: 14px; height: 14px; margin-right: 8px; fill: var(--gold); }

  .brand {
    position: absolute;
    width: 196px;
    height: 196px;
    border-radius: 50%;
    display: flex;
    align-items: center;
    justify-content: center;
    text-align: center;
    font-family: "Mulish", sans-serif;
    font-weight: 500;
    font-size: 21px;
    line-height: 28px;
    letter-spacing: 0.5px;
  }
  .brand--front { left: 436px; top: 96px; border: 2px solid var(--gold); color: var(--navy); }
  .brand--back { left: 247px; top: 80px; border: 2px solid var(--navy-soft); color: #3a4f86; }

  .tagline {
    position: absolute;
    left: 0; right: 0;
    top: 332px;
    text-align: center;
    font-family: "Mulish", sans-serif;
    font-weight: 500;
    font-size: 20px;
    color: var(--gold);
  }
</style>
</head>
<body>
<main class="stage">

  <section class="card card--front" aria-label="Business card front">
    <svg class="front-panel" viewBox="0 0 690 392" preserveAspectRatio="none" aria-hidden="true">
      <path fill="var(--gold)" d="M400 0 C 300 95 300 290 430 392 L 690 392 L 690 0 Z"/>
      <path fill="var(--paper)" d="M406 0 C 318 95 318 290 444 392 L 690 392 L 690 0 Z"/>
    </svg>

    <div class="contact">
      <h1 class="contact__name">LYDIA VANCE, M.D.</h1>
      <p class="contact__title">Board Certified Hand and Upper<br>Extremity Surgeon</p>
      <p class="contact__address">38517 North Willowmere Ave<br>Brightwater Cove, FL 33490</p>
      <ul class="contact__lines">
        <li>
          <svg viewBox="0 0 24 24" aria-label="Phone"><path d="M6.6 10.8a15.1 15.1 0 0 0 6.6 6.6l2.2-2.2c.3-.3.7-.4 1-.2 1.1.4 2.3.6 3.6.6.6 0 1 .4 1 1V20c0 .6-.4 1-1 1A17 17 0 0 1 3 4c0-.6.4-1 1-1h3.5c.6 0 1 .4 1 1 0 1.3.2 2.5.6 3.6.1.3 0 .7-.2 1z"/></svg>
          954-218-4063
        </li>
        <li>
          <svg viewBox="0 0 24 24" aria-label="Fax"><path d="M6 2h12v6H6zM3 9h18v9h-3v4H6v-4H3zm5 6v5h8v-5z"/></svg>
          954-582-7341
        </li>
        <li>
          <svg viewBox="0 0 24 24" aria-label="Email"><path d="M2 5h20v14H2zm2 2v.5l8 5.5 8-5.5V7l-8 5.5z"/></svg>
          info@myrvbonecare.example
        </li>
      </ul>
    </div>

    <div class="brand brand--front">RV Bone &amp;<br>Vitality<br>Center</div>
  </section>

  <section class="card card--back" aria-label="Business card back">
    <div class="brand brand--back">RV Bone &amp;<br>Vitality<br>Center</div>
    <p class="tagline">Grounded in Care. Centered on You</p>
  </section>

</main>
</body>
</html>
```